A fantastic website for a physio

We are looking for an eye catching website which can attract as many customer as possible.
We have logo designed and ready to be used in the website.
Please use the green and blue which is used in our logo for the preferred colors.
The following are the designs that I Iike:
http://www.example-clinicone.com.au/
http://www.example-rehabtwo.com.au/
We will be having other services including massage therapy, Psychology and podiatrist. You can find information about podiatry in our condition sheet.
for the address you can put Shop 5/248 Wattlebrook Street, Kelvindale. It might change but for now you can leave it until I confirm that in the next couple of days.

Logo file can be downloaded here:
https://files.example-share.net/s/qz4mtl9wkr82bvx/Logo1511.jpg?dl=0

Target Market(s)

Infant to old people.
We speak Farsi.

Industry/Entity Type

Physical Therapy

Number of Pages Required

5+ page

Font styles to use
Serif

Colors
33a6d7
abd037
e667a6

Requirements
Must have
• Home, About , our services, Conditions we treat and contact
• For home page and contacts we would like a tab that can connect to another website(bookwell) for online booking. We would like the patient's to be able to leave us massage or leave their email for monthly news letter. For the condition we treat you can use the condition sheets I have attached. For about us and home page you can use brochure I have attached.
• The other things should have include: in-line contact form, Google Map, clinic hours, newsletter sign-up etc, schema rich contact information
• Social media connection to our Facebook, Instagram and linked in
Nice to have
• Search engine optimization for Merrylands and Parramatta physiotherapy.
• We can speak English and Farsi. So is nice to have an information tab for Farsi speaking people. I can provide you with the texts.

```html
<!DOCTYPE html>
<html lang="en">
<head>
<meta charset="utf-8">
<title>Harbourline Physiotherapy</title>
<link rel="stylesheet" href="https://fonts.googleapis.com/css2?family=Oswald:wght@400;500&family=Roboto:wght@400;500;700&display=swap">
<style>
:root{
  --green:#8cc63f;
  --green-panel:#a3d163;
  --blue:#33a6d7;
  --blue-panel:#5bbde6;
  --pink:#e667a6;
  --pink-dark:#c54e8a;
  --ink:#222;
  --body:#666;
  --muted:#999;
  --band:#f3f3f3;
  --footer:#2b2b2b;
  --footer-base:#141414;
  --white:#fff;
}
*{margin:0;padding:0;box-sizing:border-box}
html,body{width:1200px;height:2486px;overflow:hidden;background:var(--white)}
body{font-family:"Roboto",Arial,sans-serif;color:var(--body)}
.page{position:relative;width:1200px;height:2486px;overflow:hidden}
.abs{position:absolute}

/* header */
.site-header{left:0;top:0;width:1200px;height:134px;background:var(--white)}
.brand{left:96px;top:38px;display:flex;align-items:center;gap:12px}
.brand-dot{width:62px;height:62px;border-radius:50%;background:var(--blue)}
.brand-name{font-size:27px;font-weight:500;color:var(--green);line-height:1.05;width:210px}
.topbar{left:678px;top:40px;display:flex;align-items:center;font-size:15px;color:var(--ink)}
.lang{display:flex;align-items:center;gap:7px}
.flag{width:18px;height:12px;background:linear-gradient(#b22234 0 50%,#fff 50%);border:1px solid #ccc}
.phone{margin-left:44px;display:flex;align-items:center;gap:8px;font-size:17px}
.socials{margin-left:38px;display:flex;gap:18px}
.socials span{width:24px;height:24px;border-radius:4px;background:#7a8a99}
.main-nav{left:517px;top:84px;display:flex;font-size:16px;color:var(--ink)}
.main-nav a{color:inherit;text-decoration:none;margin-right:40px}
.main-nav a.active{color:var(--green)}
.main-nav a:last-child{margin-right:0}

/* hero */
.hero{left:0;top:134px;width:1200px;height:582px;background:linear-gradient(100deg,#6b4a3a 0%,#c99a82 30%,#e8c8b4 55%,#efe6df 80%,#f4f1ee 100%)}
.hero-title{left:88px;top:558px;font-family:"Oswald",Arial,sans-serif;font-size:42px;line-height:50px;color:var(--white);font-weight:500;letter-spacing:-.5px}
.appointment{left:812px;top:254px;width:298px;height:309px;background:var(--green-panel);padding:26px 30px 0}
.panel-title{text-align:center;color:var(--white);font-size:23px;font-weight:500;margin-bottom:18px}
.field{height:45px;background:var(--white);border:1px solid #ccc;border-radius:3px;margin-bottom:10px;padding:0 14px;display:flex;align-items:center;font-size:13px;color:#777}
.btn-pink{background:var(--pink);color:var(--white);font-weight:500;display:flex;align-items:center;justify-content:center;border-radius:3px}
.appointment .btn-pink{height:44px;font-size:16px}
.slider-arrows{left:1057px;top:643px;display:flex;gap:2px}
.slider-arrows span{width:30px;height:32px;background:#333;display:flex;align-items:center;justify-content:center}

/* welcome */
.welcome{left:0;top:770px;width:1200px;text-align:center}
.section-title{font-size:30px;color:var(--ink);font-weight:400}
.section-title em{font-style:normal;color:var(--green)}
.welcome p{width:1000px;margin:18px auto 0;font-size:13.3px;line-height:22px;color:#777}

/* services */
.services{left:0;top:933px;width:1200px;height:422px;background:var(--band)}
.service{top:61px;width:300px;text-align:center}
.service-photo{width:179px;height:179px;margin:0 auto;border-radius:50%;border:4px solid var(--white);box-shadow:0 0 0 1px #ddd}
.service h3{margin-top:22px;font-size:18px;font-weight:400;color:var(--ink);letter-spacing:.5px}
.service p{width:250px;margin:14px auto 0;font-size:13.5px;line-height:21px;color:var(--muted)}
.service .more{margin-top:12px;font-size:12.5px;color:var(--green)}

/* feature */
.feature-photo{left:91px;top:1410px;width:429px;height:273px;border:3px solid #ddd;background:linear-gradient(135deg,#cfd8de,#e9ddd2 40%,#5f9fc9 70%,#dfe6ea)}
.feature-text{left:550px;top:1422px;width:558px}
.feature-text h2{font-size:21px;font-weight:500;color:var(--ink)}
.feature-text h2 em{font-style:normal;color:var(--green)}
.feature-text p{margin-top:12px;font-size:12.2px;line-height:20.7px;text-align:justify;color:#666}
.feature-text p+p{margin-top:20px}
.feature-btn{display:flex;margin-top:18px;margin-left:-2px;width:121px;height:34px;font-size:13px;box-shadow:0 2px 0 var(--pink-dark)}

/* blog */
.blog-band{left:0;top:1750px;width:1200px;height:431px;background:var(--band)}
.blog-title{left:91px;top:1783px;font-size:21px;color:var(--ink);font-weight:500}
.blog-title em{font-style:normal;color:var(--blue)}
.post{left:91px;width:650px;display:flex;gap:17px}
.post-photo{width:184px;height:133px;flex:none}
.post h4{font-size:14.5px;font-weight:400;color:var(--ink);margin-top:6px}
.post .date{font-size:12.5px;color:var(--blue);margin-top:8px}
.post p{font-size:11.8px;line-height:21px;color:#555;margin-top:6px}
.post .more{font-size:12.5px;color:var(--blue);margin-top:2px}
.quick-contact{left:809px;top:1783px;width:299px;height:364px;background:var(--blue-panel);padding:26px 29px 0}
.quick-contact .field{margin-bottom:10px}
.quick-contact .btn-pink{height:43px;font-size:16px}

/* footer */
.site-footer{left:0;top:2181px;width:1200px;height:222px;background:var(--footer);color:#ddd}
.foot-col{top:44px}
.foot-col h5{font-size:15px;font-weight:400;color:var(--white);margin-bottom:26px}
.hours{font-size:11.5px;line-height:19px;color:#ddd;border-collapse:collapse}
.hours td{padding:0}
.hours td:first-child{width:68px}
.map{width:245px;height:113px;background:linear-gradient(135deg,#dcdcdc,#c9c9c9)}
.contact-lines{font-size:11.5px;line-height:19px;color:#ddd;width:240px}
.contact-lines p{margin-bottom:14px}
.newsletter p{font-size:11.5px;line-height:17px;width:190px;margin-top:-12px}
.sub-row{display:flex;margin-top:10px}
.sub-row .email{width:146px;height:30px;background:var(--white);font-size:11.5px;color:#888;display:flex;align-items:center;padding-left:12px}
.sub-row .go{width:54px;height:30px;background:var(--pink);color:var(--white);font-size:11.5px;display:flex;align-items:center;justify-content:center}
.foot-social{display:flex;gap:14px;margin-top:16px}
.foot-social span{width:34px;height:34px;border-radius:50%;border:1px solid #bbb}
.footer-base{left:0;top:2403px;width:1200px;height:83px;background:var(--footer-base);color:var(--white);font-size:11.5px;text-align:center;line-height:83px}
</style>
</head>
<body>
<div class="page">

  <header class="site-header abs">
    <div class="brand abs"><span class="brand-dot"></span><span class="brand-name">Harbourline Physiotherapy</span></div>
    <div class="topbar abs">
      <span class="lang"><span class="flag"></span>ENGLISH
        <svg width="10" height="8" viewBox="0 0 10 8"><path d="M1 2l4 4 4-4" fill="none" stroke="#333" stroke-width="1.5"/></svg></span>
      <span class="phone">
        <svg width="14" height="14" viewBox="0 0 14 14"><rect width="14" height="14" rx="3" fill="#8cc63f"/><path d="M4 3.5c0 4 2.5 6.5 6.5 6.5l.5-1.6-1.8-.8-.8.8C7 7.8 6.2 7 5.6 5.6l.8-.8-.8-1.8z" fill="#fff"/></svg>
        0400 123 456</span>
      <span class="socials"><span></span><span></span><span></span><span></span></span>
    </div>
    <nav class="main-nav abs">
      <a class="active" href="#">HOME</a><a href="#">ABOUT US</a><a href="#">SERVICES</a><a href="#">CONDITIONS WE TREAT</a><a href="#">CONTACT</a>
    </nav>
  </header>

  <section class="hero abs" role="img" aria-label="Therapist's hands treating a patient's neck and shoulder"></section>
  <h1 class="hero-title abs">NECK PAIN CAN BE A DEBILITATING<br>HEALTH PROBLEM</h1>
  <form class="appointment abs">
    <div class="panel-title">APPOINTMENT</div>
    <div class="field">Name</div>
    <div class="field">Email id</div>
    <div class="field">Phone</div>
    <div class="btn-pink">BOOK NOW</div>
  </form>
  <div class="slider-arrows abs">
    <span><svg width="10" height="16" viewBox="0 0 10 16"><path d="M8 1L2 8l6 7" fill="none" stroke="#fff" stroke-width="1.5"/></svg></span>
    <span><svg width="10" height="16" viewBox="0 0 10 16"><path d="M2 1l6 7-6 7" fill="none" stroke="#fff" stroke-width="1.5"/></svg></span>
  </div>

  <section class="welcome abs">
    <h2 class="section-title">WELCOME TO <em>HARBOURLINE PHYSIOTHERAPY</em></h2>
    <p>We are an outpatient rehabilitation center staffed with physical therapists, massage therapists, and an athletic trainer.  We believe that during rehabilitation, the patient should be educated by their therapist in order to be able to maintain maximum flexibility and pain-free living long after our work ends. Our therapists have successfully worked with all types of injuries and we work on patients of any age. We have specialized programs for youth athletics as well as pregnancy.</p>
  </section>

  <section class="services abs">
    <div class="service abs" style="left:99px">
      <div class="service-photo" role="img" aria-label="Massage therapy on a patient's shoulder" style="background:linear-gradient(135deg,#e9e4df,#d8b8a2 60%,#b58c74)"></div>
      <h3>MASSAGE THERAPY</h3>
      <p>Lorem Ipsum has been the industry's standard dummy text ever since</p>
      <div class="more">Read More -&gt;</div>
    </div>
    <div class="service abs" style="left:451px">
      <div class="service-photo" role="img" aria-label="Therapist guiding an older patient's stretch" style="background:linear-gradient(135deg,#cfd6cf,#8bb04a 45%,#2f6f8a 80%)"></div>
      <h3>PSYCHOLOGY</h3>
      <p>Lorem Ipsum has been the industry's standard dummy text ever since</p>
      <div class="more">Read More -&gt;</div>
    </div>
    <div class="service abs" style="left:803px">
      <div class="service-photo" role="img" aria-label="Patient exercising with a small weight ball" style="background:linear-gradient(135deg,#f1ece8,#5fb2d6 50%,#d94040 80%)"></div>
      <h3>PODIATRIST</h3>
      <p>Lorem Ipsum has been the industry's standard dummy text ever since</p>
      <div class="more">Read More -&gt;</div>
    </div>
  </section>

  <div class="feature-photo abs" role="img" aria-label="Woman lying on a treatment table receiving shoulder therapy"></div>
  <article class="feature-text abs">
    <h2>SHOULDER <em>INJURIES</em></h2>
    <p>Lorem Ipsum has been the industry's standard dummy text ever since the 1500s, when an unknown printer took a galley of type and scrambled it to make a type specimen book. It has survived not only five centuries, but also the leap into electronic typesetting, remaining essentially unchanged. It was popularised in the 1960s with the release of Letterform sheets containing</p>
    <p>It has survived not only five centuries, but also the leap into electronic typesetting, remaining essentially unchanged. It was popularised in the 1960s with the release of Letterform sheets containing Lorem Ipsum passages, and more recently with desktop publishing software like Pagecraft Studio</p>
    <div class="feature-btn btn-pink">READ MORE</div>
  </article>

  <section class="blog-band abs"></section>
  <h2 class="blog-title abs">LATEST <em>BLOG</em></h2>
  <article class="post abs" style="top:1834px">
    <div class="post-photo" role="img" aria-label="Therapist treating a patient's arm" style="background:linear-gradient(135deg,#e8e2dc,#c8a894 50%,#9fd0d6)"></div>
    <div>
      <h4>Nemo Enim Ipsam Volup</h4>
      <div class="date">09-07-2016</div>
      <p>Lorem Ipsum has been the industry's standard dummy text ever since the 1500s, when an unknown printer took a galley of type and scrambled it to make a type specimen book. It has survived not only five centuries,</p>
      <div class="more">Read More »</div>
    </div>
  </article>
  <article class="post abs" style="top:1997px">
    <div class="post-photo" role="img" aria-label="Kinesiology tape applied to a patient's back" style="background:linear-gradient(135deg,#d9c2b2,#1f2a3a 55%,#2ab3b8)"></div>
    <div>
      <h4>Nemo Enim Ipsam Volup</h4>
      <div class="date">09-07-2016</div>
      <p>Lorem Ipsum has been the industry's standard dummy text ever since the 1500s, when an unknown printer took a galley of type and scrambled it to make a type specimen book. It has survived not only five centuries,</p>
      <div class="more">Read More »</div>
    </div>
  </article>
  <form class="quick-contact abs">
    <div class="panel-title">QUICK CONTACT</div>
    <div class="field">Name</div>
    <div class="field">Email id</div>
    <div class="field">Phone</div>
    <div class="field">Message</div>
    <div class="btn-pink">SUBMIT</div>
  </form>

  <footer class="site-footer abs">
    <div class="foot-col abs" style="left:89px">
      <h5>CLINIC HOURS</h5>
      <table class="hours">
        <tr><td>Monday</td><td>7:00 AM - 7:00 PM</td></tr>
        <tr><td>Tuesday</td><td>7:00 AM - 7:00 PM</td></tr>
        <tr><td>Wednesday</td><td>7:00 AM - 7:00 PM</td></tr>
        <tr><td>Thursday</td><td>7:00 AM - 7:00 PM</td></tr>
        <tr><td>Friday</td><td>7:00 AM - 7:00 PM</td></tr>
        <tr><td>Saturday</td><td>8:00 AM - 1:00 PM</td></tr>
      </table>
    </div>
    <div class="foot-col abs" style="left:328px">
      <h5>LOCATION</h5>
      <div class="map" role="img" aria-label="Street map showing the clinic location"></div>
    </div>
    <div class="foot-col abs contact-lines" style="left:654px">
      <h5>GET IN TOUCH</h5>
      <p>Address : 12/8 Ferncliff Road,<br>Kelvindale NSW 2190</p>
      <p>Phone : +61.400123456</p>
      <p>Email : hello@harbourline-example.com</p>
    </div>
    <div class="foot-col abs newsletter" style="left:910px">
      <h5>NEWSLETTER</h5>
      <p>Your about us information would fit here nicely.</p>
      <div class="sub-row"><span class="email">Email address</span><span class="go">Submit</span></div>
      <div class="foot-social"><span></span><span></span><span></span></div>
    </div>
  </footer>
  <div class="footer-base abs">Copyright © 2016. All Rights Reserved</div>

</div>
</body>
</html>
```